Media Services Start-up -- Corporate Website and Logo Design. Inspiration required!

We need a logo design and corporate website design, including coding, for our start-up business.
Vennatra’s value proposition is based on bringing together media content from a vast number of geographies globally, adding human and AI curation, translation and editing, and delivering the content using tailored customer interfaces. On the one hand, the business brings together media coverage from all over the world, and on the other it brings together content, human skills and technology to deliver a supreme customer experience.
Vennatra is a B2B media monitoring and analytics business with emphasis on global customers. Vennatra's service offering is centred around sourcing media content from different markets, processing, storing and delivering the content and insights derived from it using an online platform / mobile app.
The messaging we want to create through the logo is:
- Global scope
- Speed of delivery
- Cost-efficiency
- Multi-lingual
- Tailor-made
- Trustworthy
Target Market(s)
Business to business, PR / Communications, Media, Marketing
Logo Text
Vennatra
Coding
Coded - Design and coding required
Number of Pages Required
5+ page
Font styles to use
Other font styles liked:
- See Design Brief for details
Colors
Designer to choose colors to be used in the design.

```html
<!DOCTYPE html>
<html lang="en">
<head>
<meta charset="utf-8">
<title>Vennatra — Global Media Intelligence</title>
<link href="https://fonts.googleapis.com/css2?family=Roboto:wght@400;500;700&display=swap" rel="stylesheet">
<style>
  :root {
    --teal: #3aae9a;
    --bar: #1a1a1a;
    --ink: #ffffff;
    --muted: #d9d9d9;
    --field: #5a5a5a;
    --frame: #d4d4d4;
    --panel: #060606;
  }
  * { box-sizing: border-box; margin: 0; padding: 0; }
  html, body { width: 1200px; height: 544px; overflow: hidden; background: #000; }
  body { font-family: 'Roboto', sans-serif; color: var(--ink); position: relative; }

  .hero-visual {
    position: absolute; left: 0; top: 85px; width: 1200px; height: 423px;
    background:
      radial-gradient(circle at 700px 225px, #5b5b5b 0, #2c2c2c 110px, #151515 170px, transparent 240px),
      radial-gradient(ellipse at 200px 330px, #2a2a2a 0, transparent 420px),
      linear-gradient(180deg, #1e1e1e 0%, #0c0c0c 60%, #121212 100%);
  }

  .site-header {
    position: absolute; left: 0; top: 0; width: 1200px; height: 85px;
    background: var(--bar);
  }
  .brand {
    position: absolute; left: 141px; top: 14px;
    font-size: 48px; font-weight: 500; color: var(--muted); letter-spacing: 0;
  }
  .contact { position: absolute; top: 10px; display: flex; align-items: center; gap: 9px; font-size: 14px; }
  .contact .ring {
    width: 27px; height: 27px; border: 1.5px solid var(--muted); border-radius: 50%;
    display: flex; align-items: center; justify-content: center;
  }
  .contact-phone { left: 733px; }
  .contact-mail { left: 900px; }

  .main-nav { position: absolute; top: 54px; left: 0; font-size: 14.5px; }
  .main-nav a { position: absolute; color: var(--ink); text-decoration: none; white-space: nowrap; }
  .main-nav a.active { color: var(--teal); font-weight: 500; }
  .sign-in {
    position: absolute; left: 974px; top: 49px; width: 85px; height: 29px;
    background: var(--teal); color: var(--ink); font-size: 15.5px;
    display: flex; align-items: center; justify-content: center;
  }

  .hero-copy { position: absolute; left: 143px; top: 197px; width: 360px; }
  .hero-copy h1 { font-size: 32px; font-weight: 700; line-height: 38px; text-transform: uppercase; }
  .hero-copy p { margin-top: 11px; font-size: 15.5px; line-height: 24.7px; letter-spacing: 0.2px; }

  .lead-form {
    position: absolute; left: 752px; top: 127px; width: 304px; height: 339px;
    border: 7px solid var(--frame); background: var(--panel);
  }
  .lead-form h2 { position: absolute; left: 14px; top: 33px; font-size: 21px; font-weight: 700; white-space: nowrap; }
  .field {
    position: absolute; left: 14px; width: 263px; height: 42px; background: var(--field);
    display: flex; align-items: center; gap: 8px; padding-left: 9px; font-size: 12.5px;
  }
  .f1 { top: 79px; } .f2 { top: 136px; } .f3 { top: 194px; }
  .submit {
    position: absolute; left: 14px; top: 251px; width: 263px; height: 42px;
    background: var(--teal); display: flex; align-items: center; justify-content: center;
    font-size: 17px; font-weight: 500; text-transform: uppercase;
  }

  .site-footer {
    position: absolute; left: 0; top: 508px; width: 1200px; height: 36px; background: var(--teal);
  }
  .site-footer p { position: absolute; left: 143px; top: 10px; font-size: 13px; }
  .social { position: absolute; left: 998px; top: 11px; display: flex; gap: 9px; }
  .social span { width: 14px; height: 14px; border-radius: 50%; background: var(--ink); }
</style>
</head>
<body>
  <div class="hero-visual" role="img" aria-label="Dark monochrome city skyline with a man facing a glowing globe, surrounded by network lines and media icons"></div>

  <header class="site-header">
    <div class="brand">Vennatra</div>
    <div class="contact contact-phone">
      <span class="ring"><svg width="13" height="13" viewBox="0 0 24 24"><path fill="#fff" d="M6.6 10.8a15 15 0 006.6 6.6l2.2-2.2a1 1 0 011-.25 11.4 11.4 0 003.6.57 1 1 0 011 1V20a1 1 0 01-1 1A17 17 0 013 4a1 1 0 011-1h3.5a1 1 0 011 1c0 1.25.2 2.45.57 3.57a1 1 0 01-.25 1z"/></svg></span>
      +1 555 010 2040
    </div>
    <div class="contact contact-mail">
      <span class="ring"><svg width="13" height="10" viewBox="0 0 26 18"><rect x="1" y="1" width="24" height="16" fill="none" stroke="#fff" stroke-width="2"/><path d="M1 1l12 9 12-9" fill="none" stroke="#fff" stroke-width="2"/></svg></span>
      hello@vennatra.net
    </div>
    <nav class="main-nav">
      <a class="active" style="left:498px">Home</a>
      <a style="left:562px">Solutions</a>
      <a style="left:648px">How We Do It</a>
      <a style="left:759px">Our People</a>
      <a style="left:856px">Our Technology</a>
    </nav>
    <a class="sign-in">SIGN IN</a>
  </header>

  <section class="hero-copy">
    <h1>Delivering Global<br>Media Intelligence</h1>
    <p>Vennatra Is An International Media Intelligence Service Provider. We Help Communications Teams Build And Operate Truly Global Media Monitoring And Measurement Programmes.</p>
  </section>

  <form class="lead-form">
    <h2>Learn More About Vennatra</h2>
    <div class="field f1"><svg width="14" height="14" viewBox="0 0 24 24"><circle cx="12" cy="7" r="5" fill="#fff"/><path d="M2 23c0-6 4.5-9 10-9s10 3 10 9z" fill="#fff"/></svg>Your Name*</div>
    <div class="field f2"><svg width="14" height="10" viewBox="0 0 26 18"><rect x="1" y="1" width="24" height="16" fill="none" stroke="#fff" stroke-width="2"/><path d="M1 1l12 9 12-9" fill="none" stroke="#fff" stroke-width="2"/></svg>Your Email*</div>
    <div class="field f3"><svg width="14" height="14" viewBox="0 0 24 24"><path fill="#fff" d="M6.6 10.8a15 15 0 006.6 6.6l2.2-2.2a1 1 0 011-.25 11.4 11.4 0 003.6.57 1 1 0 011 1V20a1 1 0 01-1 1A17 17 0 013 4a1 1 0 011-1h3.5a1 1 0 011 1c0 1.25.2 2.45.57 3.57a1 1 0 01-.25 1z"/></svg>Your Phone*</div>
    <div class="submit">Get Started</div>
  </form>

  <footer class="site-footer">
    <p>Copyright © 2019 Vennatra. All Rights Reserved.</p>
    <div class="social"><span></span><span></span><span></span></div>
  </footer>
</body>
</html>
```